Redesign and move to Wordpress for corvandel.com

Our website needs a redesign and at the same time we are moving it to Wordpress. Please help us with a new digital professional look and feel.

We are an Australian Software Engineering company specialising in advanced software development using in A.I., PLatform Engineering, Integration and Cloud. See the current corvandel.com for more information about us.

```html
<!DOCTYPE html>
<html lang="en">
<head>
<meta charset="utf-8">
<title>Corvandel — Reliable Smart Software Engineering</title>
<link href="https://fonts.googleapis.com/css2?family=Urbanist:wght@400;500;600;700;800&display=swap" rel="stylesheet">
<style>
:root{
  --navy:#0c3a6d;
  --navy-deep:#0a2f5a;
  --teal:#107a7d;
  --teal-soft:#e3eeee;
  --grey-band:#efefef;
  --ink:#1d1d1d;
  --muted:#3c3c3c;
  --footer:#1c1c1c;
  --white:#ffffff;
}
*{box-sizing:border-box;margin:0;padding:0}
html,body{width:1200px;height:3891px;overflow:hidden}
body{position:relative;background:var(--white);font-family:"Urbanist",sans-serif;color:var(--ink)}
.abs{position:absolute}
.ph{position:absolute;border-radius:6px}
.teal{color:var(--teal)}

/* header */
.hero-blob{left:470px;top:0;width:730px;height:607px}
.brand{left:110px;top:30px;display:flex;align-items:center;gap:12px;font-size:30px;font-weight:500;letter-spacing:1px;color:var(--ink)}
.brand .sq{width:26px;height:26px;border:3px solid var(--ink)}
.nav{left:513px;top:42px;display:flex;gap:28px;font-size:14px;font-weight:500;text-transform:uppercase}
.nav .on{color:var(--teal)}
.search{left:920px;top:36px;width:168px;height:34px;border-radius:17px;background:#d7e6e6;font-size:12px;color:#7a8a8a;padding:10px 14px}
.search .go{position:absolute;right:4px;top:4px;width:26px;height:26px;border-radius:50%;background:#fff}

.hero-title{left:110px;top:142px;font-size:30px;font-weight:700;line-height:46px;color:var(--navy);text-transform:uppercase;letter-spacing:-.3px}
.hero-text{left:113px;top:250px;width:425px;font-size:15.5px;line-height:34.5px;color:var(--ink)}
.btn{display:flex;align-items:center;justify-content:center;gap:10px;border-radius:24px;font-weight:600;text-transform:uppercase;font-size:14px}
.btn-navy{background:var(--navy);color:#fff;border:3px solid #cfe0e6;box-shadow:0 0 0 2px var(--navy)}
.hero-btn{left:113px;top:481px;width:168px;height:38px}

/* client strip */
.clients{left:0;top:607px;width:1200px;height:106px;background:var(--grey-band);display:flex;justify-content:space-around;align-items:center;padding:0 150px;font-size:30px;font-weight:700;color:#2a2a2a}

/* services */
.section-title{left:0;width:1200px;text-align:center;font-size:33px;font-weight:700;color:var(--navy);text-transform:uppercase;letter-spacing:-.5px}
.ring{border-radius:50%;border:3px solid var(--teal)}
.dots{width:120px;height:70px;background-image:radial-gradient(#8a9aa0 1.2px,transparent 1.3px);background-size:8px 8px}
.svc-img{top:881px;width:315px;height:261px}
.svc-icon{top:1133px;width:62px;height:62px;background:var(--navy);border-radius:4px;display:flex;align-items:center;justify-content:center}
.svc-title{top:1165px;font-size:17px;font-weight:500;color:var(--navy);text-transform:uppercase}
.svc-desc{top:1198px;width:230px;font-size:14px;line-height:30px;color:var(--muted)}
.more-btn{left:471px;top:1292px;width:257px;height:44px;font-size:16px;font-weight:500}

/* about */
.about-panel{left:108px;top:1420px;width:983px;height:440px}
.about-img{left:131px;top:1446px;width:369px;height:350px;border-radius:14px}
.about-title{left:568px;top:1466px;font-size:33px;font-weight:700;color:#fff;text-transform:uppercase}
.about-title span{color:#1aa0a0}
.about-text{left:568px;top:1525px;width:500px;font-size:15.5px;line-height:34.5px;color:#fff}
.about-text p+p{margin-top:14px}
.learn-btn{left:569px;top:1737px;width:161px;height:38px;background:#fff;color:var(--navy);border:2px solid #cfe0e6;font-size:14px}

/* news */
.news-blob{left:0;top:1990px;width:520px;height:590px}
.news-img{top:2016px;width:315px;height:261px}
.date{top:2266px;width:66px;height:66px;background:var(--navy);color:#fff;text-align:center;border-radius:3px;padding-top:8px}
.date b{display:block;font-size:21px;font-weight:600}
.date small{font-size:14px;text-transform:uppercase}
.news-title{top:2294px;width:240px;font-size:18px;line-height:34px;font-weight:500;color:var(--teal);text-transform:uppercase}
.news-desc{width:245px;font-size:14px;line-height:30px;color:var(--ink)}
.arrow-dot{width:30px;height:30px;border-radius:50%;display:flex;align-items:center;justify-content:center}

/* newsletter */
.newsletter{left:110px;top:2538px;width:980px;height:346px;background:var(--navy);border-radius:26px;text-align:center;color:#fff}
.newsletter h2{margin-top:56px;font-size:32px;font-weight:700;text-transform:uppercase;letter-spacing:-.8px;line-height:56px}
.newsletter h2 span{color:#139a9c}
.newsletter p{font-size:20px;margin-top:10px}
.sub-form{position:absolute;left:253px;top:242px;width:471px;height:52px;border-radius:26px;border:1px solid #3c6490;background:#0f4277;text-align:left}
.sub-form .ph-text{position:absolute;left:18px;top:16px;font-size:15px;color:#8ba2bd;text-transform:uppercase}
.sub-form .sub-btn{position:absolute;right:2px;top:2px;width:175px;height:46px;border-radius:24px;background:var(--teal);color:#fff;font-size:15px;font-weight:700;display:flex;align-items:center;justify-content:center;text-transform:uppercase}

/* booking */
.book-title{left:0;top:2952px;width:1200px;text-align:center;font-size:32px;font-weight:700;line-height:57px;color:var(--navy);text-transform:uppercase;letter-spacing:-.8px}
.book-card{left:110px;top:3110px;width:978px;height:433px;border-radius:22px;overflow:hidden;box-shadow:0 0 0 1px #eee}
.cal{position:absolute;left:0;top:0;width:490px;height:433px;background:#fff}
.cal-head{position:absolute;left:0;top:46px;width:490px;display:flex;justify-content:center;gap:22px;align-items:center;font-size:21px;font-weight:600;color:var(--navy)}
.cal table{position:absolute;left:18px;top:100px;width:450px;border-collapse:collapse;text-align:center}
.cal th{font-size:15px;font-weight:500;color:var(--teal);height:34px}
.cal td{font-size:13px;height:59px;color:#333}
.cal td.sel span{display:inline-block;width:30px;height:30px;line-height:30px;border-radius:50%;background:var(--navy);color:#fff}
.meet{position:absolute;left:490px;top:0;width:488px;height:433px;background:var(--navy);color:#fff;text-transform:uppercase}
.meet .avatar{position:absolute;left:42px;top:46px;width:116px;height:112px;border-radius:6px}
.meet .who{position:absolute;left:193px;top:100px;font-size:18px;font-weight:700;letter-spacing:-.5px}
.meet .row{position:absolute;left:40px;font-size:17px;font-weight:700;letter-spacing:-.5px}
.meet .row small{font-size:13px;font-weight:600;margin-left:14px}

/* footer */
.footer{left:0;top:3627px;width:1200px;height:264px;background:var(--footer);color:#fff}
.footer .brand{color:#fff;left:103px;top:52px;font-size:36px}
.footer .brand .sq{border-color:#fff;width:32px;height:32px}
.footer .copy{position:absolute;left:103px;top:136px;font-size:13px;line-height:30px}
.fcol{position:absolute;top:54px}
.fcol h4{font-size:17px;font-weight:500;color:var(--teal);text-transform:uppercase;margin-bottom:16px}
.fcol li{list-style:none;font-size:13px;line-height:35px}
.contact-row{display:flex;align-items:center;gap:24px;font-size:13px;line-height:30px;margin-bottom:16px}
.contact-row .ic{width:38px;height:38px;background:#333;display:flex;align-items:center;justify-content:center;flex:none}
</style>
</head>
<body>

<!-- hero -->
<svg class="abs hero-blob" viewBox="0 0 730 607" aria-hidden="true">
  <path d="M240 0 H730 V607 H20 C60 520 110 420 120 330 C130 230 150 80 240 0 Z" fill="var(--teal-soft)"/>
</svg>
<div class="abs brand"><span class="sq"></span>corvandel</div>
<nav class="abs nav"><span class="on">Home</span><span>Services</span><span>About</span><span>Blog</span><span>Contact</span></nav>
<div class="abs search">Search here<span class="go"></span></div>

<h1 class="abs hero-title">Reliable <span class="teal">Smart Software</span><br>Engineering</h1>
<p class="abs hero-text">At Corvandel, we craft bespoke software solutions that are not available on the market. By building organizations market-leading products, process automation, legacy system enablement, or advanced intelligent systems, we empower our customers to achieve a competitive edge in their industry.</p>
<div class="abs btn btn-navy hero-btn">Get Started
  <svg width="14" height="12" viewBox="0 0 14 12"><path d="M1 6h11M7 1l5 5-5 5" stroke="#fff" stroke-width="2" fill="none"/></svg></div>

<div class="ph" style="left:628px;top:101px;width:219px;height:155px;background:linear-gradient(135deg,#2d5a7c,#c9d6df)" role="img" aria-label="Developer working at a laptop"></div>
<div class="ph" style="left:626px;top:277px;width:221px;height:286px;background:linear-gradient(160deg,#0c2a55,#1b4c8c)" role="img" aria-label="Close-up of source code on a screen"></div>
<div class="ph" style="left:867px;top:103px;width:221px;height:288px;background:linear-gradient(150deg,#0b3a6b,#1d7fbf)" role="img" aria-label="Hands on a laptop with glowing AI and LLM icons"></div>
<div class="ph" style="left:867px;top:411px;width:221px;height:156px;background:linear-gradient(135deg,#2f3b45,#b9c3c9)" role="img" aria-label="Smiling engineer beside a monitor showing code"></div>

<!-- clients -->
<div class="abs clients">
  <span>Brightwell</span><span>Northgate</span><span>Haulmark</span><span>Solvane</span>
</div>

<!-- services -->
<div class="abs dots" style="left:48px;top:762px"></div>
<div class="abs ring" style="left:992px;top:783px;width:20px;height:20px"></div>
<h2 class="abs section-title" style="top:790px">Corvandel <span class="teal">Services</span></h2>

<div class="ph svc-img" style="left:110px;background:linear-gradient(180deg,#2a6fd0,#0d1f4f)" role="img" aria-label="Glowing cloud above a night city skyline"></div>
<div class="ph svc-img" style="left:443px;background:linear-gradient(135deg,#2d6d86,#a9d0e0)" role="img" aria-label="Engineer working on a transparent digital interface"></div>
<div class="ph svc-img" style="left:772px;background:linear-gradient(135deg,#cfc6bb,#f2ede6)" role="img" aria-label="Support agent wearing a headset"></div>

<div class="abs svc-icon" style="left:110px"><svg width="34" height="34" viewBox="0 0 34 34" fill="none" stroke="#fff" stroke-width="2"><circle cx="17" cy="17" r="6"/><circle cx="17" cy="4" r="2.5"/><circle cx="17" cy="30" r="2.5"/><circle cx="4" cy="17" r="2.5"/><circle cx="30" cy="17" r="2.5"/><path d="M17 7v4M17 23v4M7 17h4M23 17h4"/></svg></div>
<div class="abs svc-icon" style="left:443px"><svg width="34" height="34" viewBox="0 0 34 34" fill="none" stroke="#fff" stroke-width="2"><circle cx="17" cy="17" r="7"/><circle cx="17" cy="17" r="3"/><path d="M17 4v5M17 25v5M4 17h5M25 17h5M8 8l3 3M23 23l3 3M8 26l3-3M23 11l3-3"/></svg></div>
<div class="abs svc-icon" style="left:772px"><svg width="34" height="34" viewBox="0 0 34 34" fill="none" stroke="#fff" stroke-width="2"><path d="M9 30v-6c-3-2-5-6-5-10a12 12 0 0 1 24 0l3 6h-3v5h-5v5"/><circle cx="16" cy="13" r="4"/></svg></div>

<div class="abs svc-title" style="left:204px">Microservices</div>
<div class="abs svc-title" style="left:536px">Platform Engineering</div>
<div class="abs svc-title" style="left:866px">A.I. Agents</div>
<p class="abs svc-desc" style="left:204px">Microservices is an architectural style that structures</p>
<p class="abs svc-desc" style="left:536px">Platform engineering involves creating and managing</p>
<p class="abs svc-desc" style="left:866px">An AI agent is a software application that interacts</p>

<div class="abs btn btn-navy more-btn">View More Services
  <svg width="16" height="14" viewBox="0 0 16 14"><path d="M1 7h13M8 1l6 6-6 6" stroke="#fff" stroke-width="2" fill="none"/></svg></div>
<div class="abs ring" style="left:247px;top:1329px;width:34px;height:34px;border-color:var(--navy);border-width:4px"></div>
<div class="abs dots" style="left:1032px;top:1310px"></div>

<!-- about -->
<svg class="abs about-panel" viewBox="0 0 983 440" aria-hidden="true">
  <path d="M22 2 H968 Q981 2 981 15 V380 Q981 403 958 403 H540 C500 403 490 440 442 440 C394 440 384 403 344 403 H2 V20 Q2 2 22 2 Z" fill="var(--navy)"/>
  <path d="M432 410 l10 9 10-9" stroke="#fff" stroke-width="2.4" fill="none"/>
</svg>
<div class="ph about-img" style="background:linear-gradient(135deg,#3b4e5f,#c3ccd4)" role="img" aria-label="Software team collaborating at computers"></div>
<h2 class="abs about-title">About <span>Corvandel</span></h2>
<div class="abs about-text">
  <p>Since our inception in 2013, we have been on a mission to make complex custom enterprise integration accessible to any organization, regardless of industry, size, or location.</p>
  <p>Our journey began with a focus on Integration Architecture, quickly moving into delivering bespoke systems integration</p>
</div>
<div class="abs btn learn-btn">Learn More
  <svg width="14" height="12" viewBox="0 0 14 12"><path d="M1 6h11M7 1l5 5-5 5" stroke="#0c3a6d" stroke-width="2" fill="none"/></svg></div>

<!-- news -->
<svg class="abs news-blob" viewBox="0 0 520 590" aria-hidden="true">
  <path d="M0 20 C120 60 180 140 260 180 C380 240 470 330 440 460 C420 540 350 575 260 582 H0 Z" fill="#eef4f4"/>
</svg>
<h2 class="abs section-title" style="top:1920px">News &amp; <span class="teal">Articles</span></h2>

<div class="abs arrow-dot" style="left:38px;top:2132px;background:var(--teal)"><svg width="12" height="12" viewBox="0 0 12 12"><path d="M8 1 3 6l5 5" stroke="#fff" stroke-width="2" fill="none"/></svg></div>
<div class="abs arrow-dot" style="left:1128px;top:2132px;background:var(--navy)"><svg width="12" height="12" viewBox="0 0 12 12"><path d="M4 1l5 5-5 5" stroke="#fff" stroke-width="2" fill="none"/></svg></div>
<div class="abs ring" style="left:-14px;top:2390px;width:24px;height:24px;border-color:var(--navy)"></div>

<div class="ph news-img" style="left:112px;background:linear-gradient(135deg,#6e5a73,#c6a9b8)" role="img" aria-label="Weathered server building with integration signage"></div>
<div class="ph news-img" style="left:444px;background:linear-gradient(135deg,#cfd6dc,#5f6b75)" role="img" aria-label="Team meeting beneath an integration architecture diagram"></div>
<div class="ph news-img" style="left:774px;background:linear-gradient(135deg,#2a3140,#c9d3dd)" role="img" aria-label="Server rack beside stacks of paper and a worried engineer"></div>

<div class="abs date" style="left:112px"><b>24</b><small>May</small></div>
<div class="abs date" style="left:444px"><b>21</b><small>June</small></div>
<div class="abs date" style="left:774px"><b>26</b><small>May</small></div>

<div class="abs news-title" style="left:206px">Why is FlowLink dead?</div>
<div class="abs news-title" style="left:537px">Meet Corvandel: The FlowLink Experts</div>
<div class="abs news-title" style="left:868px">Top Reasons FlowLink Server Runtime Can Fail in Production</div>
<p class="abs news-desc" style="left:206px;top:2367px">In the ever-evolving world of technology, keeping up...</p>
<p class="abs news-desc" style="left:537px;top:2367px">At Corvandel, we pride ourselves on having a team of exceptional...</p>
<p class="abs news-desc" style="left:868px;top:2403px">As a FlowLink expert with extensive experience in deploying...</p>

<!-- newsletter -->
<section class="abs newsletter">
  <h2>Australia's Largest Health Charity Implements<br><span>Corvandel API Msg Bus</span></h2>
  <p>Register to our newsletter to find out more.</p>
  <div class="sub-form"><span class="ph-text">Email Address</span><span class="sub-btn">Subscribe Now</span></div>
</section>

<!-- booking -->
<h2 class="abs book-title">Book an obligation free consultation <span class="teal">with</span><br><span class="teal">our lead technologist</span></h2>
<div class="abs book-card">
  <div class="cal">
    <div class="cal-head">
      <svg width="16" height="12" viewBox="0 0 16 12"><path d="M15 6H2M6 1 1 6l5 5" stroke="#107a7d" stroke-width="2" fill="none"/></svg>
      January 2025
      <svg width="16" height="12" viewBox="0 0 16 12"><path d="M1 6h13M10 1l5 5-5 5" stroke="#107a7d" stroke-width="2" fill="none"/></svg>
    </div>
    <table>
      <tr><th>SUN</th><th>MON</th><th>TUE</th><th>WED</th><th>THU</th><th>FRI</th><th>SAT</th></tr>
      <tr><td></td><td></td><td></td><td>1</td><td>2</td><td>3</td><td>4</td></tr>
      <tr><td>5</td><td>6</td><td>7</td><td>8</td><td>9</td><td>10</td><td class="sel"><span>11</span></td></tr>
      <tr><td>12</td><td>13</td><td>14</td><td>15</td><td>16</td><td>17</td><td>18</td></tr>
      <tr><td>19</td><td>20</td><td>21</td><td>22</td><td>23</td><td>24</td><td>25</td></tr>
      <tr><td>26</td><td>27</td><td>28</td><td>29</td><td>30</td><td>31</td><td></td></tr>
    </table>
  </div>
  <div class="meet">
    <div class="avatar" style="background:linear-gradient(135deg,#6b5646,#d3c2b3)" role="img" aria-label="Portrait of the chief technology officer"></div>
    <div class="who">Meet with our CTO</div>
    <div class="row" style="top:208px">Meeting Duration :<small>30 Minutes</small></div>
    <div class="row" style="top:262px">What time works best?</div>
    <div class="row" style="top:305px;font-size:13px;font-weight:600">Showing times for January 15, 2025</div>
    <div class="row" style="top:351px">UTC +05:30 New Delhi, Mumbai, Calcutta <small style="margin-left:6px">▾</small></div>
  </div>
</div>

<!-- footer -->
<footer class="abs footer">
  <div class="abs brand"><span class="sq"></span>corvandel</div>
  <div class="copy">@2024 Copyrights Corvandel.<br>All Rights Reserved</div>
  <div class="fcol" style="left:457px"><h4>Quick Links</h4><ul><li>Services</li><li>Contact</li><li>About</li><li>Blog</li></ul></div>
  <div class="fcol" style="left:671px"><h4>Other Links</h4><ul><li>Privacy Policy</li><li>Site Map</li><li>Terms of Use</li><li>Blog</li></ul></div>
  <div class="fcol" style="left:885px"><h4>Contact Us</h4>
    <div class="contact-row"><span class="ic"><svg width="16" height="16" viewBox="0 0 24 24"><path d="M6.6 10.8a15 15 0 0 0 6.6 6.6l2.2-2.2c.3-.3.7-.4 1-.2 1.1.4 2.3.6 3.6.6.6 0 1 .4 1 1V20c0 .6-.4 1-1 1A17 17 0 0 1 3 4c0-.6.4-1 1-1h3.5c.6 0 1 .4 1 1 0 1.3.2 2.5.6 3.6.1.3 0 .7-.2 1z" fill="#fff"/></svg></span>1800 555 019</div>
    <div class="contact-row"><span class="ic"><svg width="16" height="18" viewBox="0 0 24 26"><path d="M12 1a8 8 0 0 0-8 8c0 6 8 14 8 14s8-8 8-14a8 8 0 0 0-8-8z" fill="#fff"/><circle cx="12" cy="9" r="3" fill="#333"/></svg></span>Suite 210, 48 Harbour Lane<br>Melbourne, VIC , 3000</div>
  </div>
</footer>

</body>
</html>
```